Business Card Design for a Software Startup

We'd like to have a business card design. We already have a logo. Basically what we need is a clean design with name, address, cellphone and phone numbers, e-mail and web site address (front) and a space on the back with our logo with the company name on the right side and some texts on the bottom.
We are a development and consulting company in Brazil with highly qualified team of professionals in Java, iOS and Android development and consulting.

Target Market(s)

CIO, IT managers of mid to big size companies

Industry/Entity Type

Business

```html
<!DOCTYPE html>
<html lang="en">
<head>
<meta charset="utf-8">
<title>ZOVREK Business Card</title>
<link rel="stylesheet" href="https://fonts.googleapis.com/css2?family=Source+Sans+3:wght@400;600;700&display=swap">
<style>
  :root {
    --canvas: #eceef1;
    --white: #ffffff;
    --navy: #1a3a74;
    --deep-navy: #263a78;
    --blue: #1f6fc0;
    --sky: #14a2e4;
    --ink-dark: #17305f;
    --card-shadow: rgba(20, 40, 80, 0.18);
  }
  * { box-sizing: border-box; margin: 0; padding: 0; }
  html, body {
    width: 1200px;
    height: 720px;
    overflow: hidden;
    background: var(--canvas);
    font-family: "Source Sans 3", Arial, sans-serif;
  }
  .canvas {
    position: relative;
    width: 1200px;
    height: 720px;
    display: flex;
    align-items: center;
    justify-content: center;
    gap: 44px;
  }
  .card {
    position: relative;
    width: 525px;
    height: 300px;
    overflow: hidden;
    box-shadow: 0 10px 26px var(--card-shadow);
  }

  /* Front */
  .card-front { background: var(--white); }
  .card-front .backdrop {
    position: absolute;
    inset: 0;
    width: 100%;
    height: 100%;
  }
  .brand-block {
    position: absolute;
    left: 0;
    width: 250px;
    top: 76px;
    display: flex;
    flex-direction: column;
    align-items: center;
    gap: 12px;
  }
  .brand-square {
    width: 92px;
    height: 92px;
    border-radius: 14px;
    background: var(--blue);
  }
  .brand-name {
    font-weight: 700;
    font-size: 40px;
    letter-spacing: 1px;
    color: var(--ink-dark);
    line-height: 1;
  }
  .contact {
    position: absolute;
    right: 30px;
    top: 26px;
    text-align: right;
    color: var(--white);
  }
  .contact .person-name {
    font-weight: 700;
    font-size: 22px;
    line-height: 1.05;
  }
  .contact .person-title {
    font-size: 14px;
    margin-bottom: 10px;
  }
  .contact-line {
    display: flex;
    justify-content: flex-end;
    align-items: center;
    gap: 5px;
    font-size: 13.5px;
    line-height: 17px;
  }
  .contact-line svg { width: 11px; height: 11px; flex: none; }
  .address {
    margin-top: 8px;
    font-size: 13.5px;
    line-height: 17px;
  }

  /* Back */
  .card-back {
    background: linear-gradient(32deg, var(--sky) 0%, var(--blue) 48%, var(--deep-navy) 100%);
  }
  .back-brand {
    position: absolute;
    left: 0;
    right: 0;
    top: 58px;
    display: flex;
    flex-direction: column;
    align-items: center;
    gap: 14px;
  }
  .back-brand .brand-square {
    width: 120px;
    height: 120px;
    border-radius: 16px;
    background: var(--white);
  }
  .back-brand .brand-name {
    color: var(--white);
    font-size: 34px;
  }
  .back-url {
    position: absolute;
    left: 0;
    right: 0;
    bottom: 28px;
    text-align: center;
    color: var(--white);
    font-size: 17px;
    letter-spacing: 4px;
  }
</style>
</head>
<body>
<main class="canvas">

  <section class="card card-front" aria-label="Business card front">
    <svg class="backdrop" viewBox="0 0 525 300" preserveAspectRatio="none" aria-hidden="true">
      <defs>
        <linearGradient id="front-blue" x1="0" y1="1" x2="1" y2="0">
          <stop offset="0" stop-color="#14a2e4"/>
          <stop offset="0.5" stop-color="#1f6fc0"/>
          <stop offset="1" stop-color="#263a78"/>
        </linearGradient>
      </defs>
      <path d="M250 0 C335 90 335 210 262 300 L525 300 L525 0 Z" fill="url(#front-blue)"/>
      <path d="M240 0 C324 90 324 210 252 300" fill="none" stroke="#ffffff" stroke-width="10"/>
      <path d="M232 0 C316 90 316 210 244 300" fill="none" stroke="#1a3a74" stroke-width="8"/>
      <path d="M224 0 C308 90 308 210 236 300" fill="none" stroke="#ffffff" stroke-width="6"/>
    </svg>

    <div class="brand-block">
      <span class="brand-square"></span>
      <span class="brand-name">ZOVREK</span>
    </div>

    <div class="contact">
      <p class="person-name">Your Name</p>
      <p class="person-title">Title</p>
      <p class="contact-line">
        <svg viewBox="0 0 12 12" aria-hidden="true"><circle cx="6" cy="6" r="5.2" fill="none" stroke="#fff" stroke-width="1.2"/><path d="M4 3.5 L5 3.5 L5.5 5 L4.8 5.6 Q5.6 7 6.6 7.4 L7.2 6.7 L8.6 7.2 L8.6 8.2 Q5 8.6 4 3.5 Z" fill="#fff"/></svg>
        123-456-7890
      </p>
      <p class="contact-line">
        <svg viewBox="0 0 12 12" aria-hidden="true"><rect x="3" y="1" width="6" height="10" rx="1.2" fill="none" stroke="#fff" stroke-width="1.2"/><circle cx="6" cy="9" r="0.8" fill="#fff"/></svg>
        456-085-4321
      </p>
      <p class="contact-line">
        <svg viewBox="0 0 12 12" aria-hidden="true"><rect x="1" y="2.5" width="10" height="7" rx="1" fill="#fff"/><path d="M1.5 3 L6 6.6 L10.5 3" fill="none" stroke="#1f6fc0" stroke-width="1"/></svg>
        yourname@zovrek.com
      </p>
      <p class="contact-line">
        <svg viewBox="0 0 12 12" aria-hidden="true"><circle cx="6" cy="6" r="5" fill="none" stroke="#fff" stroke-width="1.1"/><ellipse cx="6" cy="6" rx="2.2" ry="5" fill="none" stroke="#fff" stroke-width="0.9"/><path d="M1 6 H11" stroke="#fff" stroke-width="0.9"/></svg>
        www.zovrek.com
      </p>
      <div class="address">
        <p>Door No. Street Name</p>
        <p>City Name</p>
        <p>State, Zip Code</p>
      </div>
    </div>
  </section>

  <section class="card card-back" aria-label="Business card back">
    <div class="back-brand">
      <span class="brand-square"></span>
      <span class="brand-name">ZOVREK</span>
    </div>
    <p class="back-url">www.zovrek.com</p>
  </section>

</main>
</body>
</html>
```